Sunset Harbor Living Web Page

We need a web page design that has two intro pages - first being a 'home page', then a link to the second page that has the 'content tabs' and a 'call to action' (see below).

The business helps people that wish to retire to S.E.Asia (Thailand, Malaysia, Indonesia,The Philippines etc) - to enjoy the lifestyle and the remaining years of their lives. What attracts S.E.Asia to many people is the lower cost, the atmoshpere and beauty of the tropics and the vibrancy of the various countries.

People that are wishing to make the most of their retirement and are adventurous at a great bargain compared to the cost of their own countries will be interested.

We help them achieve this - visa, financials (tax, gov't payments etc), introduce them to the right people for property, clubs, retirement facilities, insurance and so forth.

Therefore we are providing an extremely wide ranging service and this site will provide broad but general information only - with a call to action to come and see us for more specific information and how we can help them specifically.

This site will be predominantly for travel and lifestyle, it will be linked with another financial services (financial planning) site later down the track.

The colour scheme is dark green and blue - as per the attached logo design. Photos and background just think lifestyle and S.E.Asia - beaches/mountains/water/recreational activities for retirees.

Target market is mostly those coming up to retirement to those that are already retired. But we also expect to have some interest with younger people that would like to find out more and plan for the future. So a broad age group but I would say mostly 40-70 yrs old.

On the first (Home) page we would like our company name 'Sunset Harbor Living', our logo (which will be on all pages) and a statement such as: “Imagine a retirement where your dreams are brought to life, and you have never felt more alive. Let us show you how”. Then a link to the second page.

We would like an uncluttered site. On the second (contents) page the tabs would be:

- Visa
- Property
- Financials
- Travel
- Insurance & Healthcare
- Medical Tourism
- Cost of living
- Weekly Blogs and articles
- Sunset Harbor Living story

We would also like a call to action on the second page - asking them to leave their contact details if they wish to learn more or sign up to our weekly newsletter/blog.

We are open to suggestions and your imaginations.

Thank you
Malcolm

Font styles to use
Serif
Script

Colors
0255a3
3377b5
00a990
9bcb3c
abd036
33b8a4
85abd2
cadf82
86cfc6

Requirements
Must have
• I have been asked by the web designer to receive a 'Web Font' so that we can 'get off of Zentrofy'. Hope that makes sense.

```html
<!DOCTYPE html>
<html lang="en">
<head>
<meta charset="utf-8">
<title>Sunset Harbor Living — Home</title>
<link rel="stylesheet" href="https://fonts.googleapis.com/css2?family=Oswald:wght@300;400&family=Raleway:wght@400;500;600;700&display=swap">
<style>
  :root {
    --green-top: #0cb25c;
    --green-bottom: #019a4c;
    --green-line: #06893f;
    --blue: #0a8fd6;
    --white: #ffffff;
    --footer-bg: rgba(40, 40, 36, 0.72);
    --photo-dark: #3e4226;
    --photo-mid: #8a8a3c;
    --photo-light: #c9c46a;
  }
  * { margin: 0; padding: 0; box-sizing: border-box; }
  html, body { width: 1200px; height: 750px; overflow: hidden; }
  body { font-family: "Raleway", sans-serif; color: var(--white); }

  .page { position: relative; width: 1200px; height: 750px; overflow: hidden; }

  .hero-photo {
    position: absolute; inset: 0;
    background:
      radial-gradient(ellipse 420px 520px at 900px 420px, rgba(185,180,150,0.55), transparent 70%),
      radial-gradient(ellipse 500px 300px at 1050px 200px, rgba(200,196,90,0.7), transparent 70%),
      radial-gradient(ellipse 600px 400px at 420px 180px, rgba(160,150,60,0.55), transparent 70%),
      linear-gradient(180deg, var(--photo-mid) 0%, #7a7a3a 45%, #6c6238 70%, #8a7d4e 100%);
  }
  .hero-photo::after {
    content: ""; position: absolute; inset: 0;
    background: linear-gradient(90deg, rgba(40,40,20,0.45) 0%, rgba(40,40,20,0.15) 55%, rgba(0,0,0,0) 100%);
  }

  .site-header {
    position: absolute; top: 0; left: 0; width: 100%; height: 83px;
    background: linear-gradient(180deg, var(--green-top), var(--green-bottom));
    border-bottom: 3px solid var(--green-line);
    box-shadow: 0 2px 6px rgba(0,0,0,0.25);
  }

  .brand-badge {
    position: absolute; left: 475px; top: -105px; width: 252px; height: 252px;
    border-radius: 50%;
    background: linear-gradient(180deg, #ffffff 55%, #e6e6e6 100%);
    border: 3px solid var(--white);
    box-shadow: 0 2px 6px rgba(0,0,0,0.2);
    display: flex; flex-direction: column; align-items: center; justify-content: flex-end;
    padding-bottom: 40px;
  }
  .brand-mark { width: 54px; height: 54px; border-radius: 50%; background: var(--green-bottom); margin-bottom: 10px; }
  .brand-name { font-family: "Raleway", sans-serif; font-weight: 700; font-size: 19px; color: var(--blue); }

  .social {
    position: absolute; top: 28px; left: 865px;
    display: flex; align-items: center; gap: 6px;
    font-size: 14px;
  }
  .social-label { margin-right: 10px; }
  .social-dot {
    width: 28px; height: 28px; border-radius: 50%;
    background: var(--green-line);
    border: 1px solid rgba(255,255,255,0.35);
  }

  .intro { position: absolute; left: 131px; top: 266px; width: 520px; }
  .intro-statement {
    font-family: "Oswald", sans-serif; font-weight: 300;
    font-size: 32px; line-height: 44px; color: var(--white);
  }
  .intro-statement strong { font-weight: 400; }

  .enter-button {
    position: absolute; left: 131px; top: 433px; width: 175px; height: 46px;
    background: linear-gradient(180deg, #ffffff, #e4e4e4);
    border-radius: 3px;
    box-shadow: 0 2px 4px rgba(0,0,0,0.35);
    display: flex; align-items: center; justify-content: center; gap: 16px;
    color: var(--blue); font-size: 19px; font-weight: 500; text-decoration: none;
  }
  .enter-button svg { display: block; }

  .site-footer {
    position: absolute; left: 0; top: 688px; width: 100%; height: 62px;
    background: var(--footer-bg);
    display: flex; align-items: center; justify-content: center;
    font-size: 14px;
  }
</style>
</head>
<body>
<div class="page">
  <div class="hero-photo" role="img" aria-label="Photo of a relaxed retiree in a straw hat reclining on a park bench among sunlit autumn trees"></div>

  <header class="site-header">
    <div class="social">
      <span class="social-label">Follow us:</span>
      <span class="social-dot"></span>
      <span class="social-dot"></span>
      <span class="social-dot"></span>
      <span class="social-dot"></span>
    </div>
  </header>

  <div class="brand-badge">
    <span class="brand-mark"></span>
    <span class="brand-name">Sunset Harbor Living</span>
  </div>

  <section class="intro">
    <p class="intro-statement"><strong>Imagine a retirement where your Dreams</strong> are brought to life, and you have never felt more alive. <strong>Let us show you how</strong></p>
  </section>

  <a class="enter-button" href="#">Enter Site
    <svg width="22" height="22" viewBox="0 0 22 22" aria-hidden="true">
      <circle cx="11" cy="11" r="11" fill="#00a94f"/>
      <path d="M9 6.5 L13.5 11 L9 15.5" stroke="#fff" stroke-width="2.6" fill="none" stroke-linecap="round" stroke-linejoin="round"/>
    </svg>
  </a>

  <footer class="site-footer">Copyright © 2016 Sunsetharborliving Ltd. All Right Reserved</footer>
</div>
</body>
</html>
```